Structural Engineering Business Card

Brookvane Drafting does residential house plans for clients in Central Florida. Would like simple but elegant business card that is appropriate for a house plan engineering company. Prefer black business card with black/white them but open to other shades of blue. I uploaded a sample card that I came across that looked good but please come up with your own creative designs.

Contact Information for Business Card

Name, Title, Phone, Email, Address, website

```html
<!DOCTYPE html>
<html lang="en">
<head>
<meta charset="utf-8">
<title>Brookvane Drafting – Business Card</title>
<link rel="stylesheet" href="https://fonts.googleapis.com/css2?family=Oswald:wght@600&family=Poppins:wght@400;700&display=swap">
<style>
  :root {
    --stage: #2c2c2c;
    --card: #111111;
    --ink: #ffffff;
    --ink-soft: #e6e6e6;
  }
  * { box-sizing: border-box; margin: 0; padding: 0; }
  html, body { width: 1200px; height: 900px; overflow: hidden; }
  body {
    background: var(--stage);
    display: flex;
    flex-direction: column;
    align-items: center;
    justify-content: center;
    gap: 40px;
    font-family: "Poppins", sans-serif;
    color: var(--ink);
  }
  .card {
    position: relative;
    width: 680px;
    height: 380px;
    background: var(--card);
    border-bottom: 16px solid var(--ink);
    box-shadow: 0 12px 30px rgba(0,0,0,.45);
  }
  .card--front {
    display: flex;
    align-items: center;
    justify-content: center;
  }
  .brand {
    display: flex;
    align-items: center;
    gap: 18px;
  }
  .brand__mark {
    width: 40px;
    height: 40px;
    background: var(--ink);
  }
  .brand__name {
    font-family: "Poppins", sans-serif;
    font-weight: 700;
    font-size: 46px;
    letter-spacing: 0.5px;
    color: var(--ink);
  }
  .card--back .details {
    position: absolute;
    left: 80px;
    top: 150px;
    display: flex;
    align-items: stretch;
  }
  .person {
    text-align: right;
    padding-right: 26px;
    padding-top: 2px;
  }
  .person__name {
    font-family: "Oswald", sans-serif;
    font-weight: 600;
    font-size: 30px;
    line-height: 1.1;
    text-transform: uppercase;
    letter-spacing: 0.3px;
  }
  .person__title {
    font-size: 18px;
    color: var(--ink-soft);
  }
  .divider {
    width: 1.5px;
    background: var(--ink);
    margin-right: 26px;
  }
  .contact { list-style: none; padding: 4px 0; }
  .contact li {
    display: flex;
    align-items: center;
    gap: 10px;
    font-size: 19px;
    line-height: 1.45;
  }
  .contact svg { width: 18px; height: 18px; flex: none; }
  .address {
    position: absolute;
    left: 80px;
    top: 275px;
    font-size: 19px;
  }
</style>
</head>
<body>
  <section class="card card--front">
    <div class="brand">
      <span class="brand__mark"></span>
      <span class="brand__name">Brookvane Drafting</span>
    </div>
  </section>

  <section class="card card--back">
    <div class="details">
      <div class="person">
        <h1 class="person__name">Daniel Whitmore</h1>
        <p class="person__title">Managing Director</p>
      </div>
      <div class="divider"></div>
      <ul class="contact">
        <li>
          <svg viewBox="0 0 24 24" fill="none" stroke="#fff" stroke-width="2" aria-hidden="true"><path d="M5 3h4l2 5-2.5 1.5a11 11 0 0 0 6 6L16 13l5 2v4a2 2 0 0 1-2 2A17 17 0 0 1 3 5a2 2 0 0 1 2-2z"/></svg>
          044-555 010 220
        </li>
        <li>
          <svg viewBox="0 0 24 24" fill="none" stroke="#fff" stroke-width="2" aria-hidden="true"><rect x="3" y="5" width="18" height="14"/><path d="M3 5l9 8 9-8"/></svg>
          info@brookvane.com
        </li>
        <li>
          <svg viewBox="0 0 24 24" fill="none" stroke="#fff" stroke-width="2" aria-hidden="true"><circle cx="12" cy="12" r="9"/><path d="M3 12h18M12 3c3 3 3 15 0 18M12 3c-3 3-3 15 0 18"/></svg>
          www.brookvane.com
        </li>
      </ul>
    </div>
    <p class="address">118 Orchard Lane, Lakeview, Florida, 32801</p>
  </section>
</body>
</html>
```